Corvel Capital LLC

Need Professional Business cards for New Investment Fund

Target Market(s)

High Quality investors

Industry/Entity Type

Financial

Contact Information for Business Card

Phone Number +1 555 284 6190
Name Lukas Varenko
Title Fund Manager
email lv@FundCorvel.com
Website www.FundCorvel.com

Colors

Designer to choose colors to be used in the design.

Requirements
Must have
• Must have our Logo and all of the above. Must be made so lettering and loge can be raised

```html
<!DOCTYPE html>
<html lang="en">
<head>
<meta charset="utf-8">
<title>Corvel Capital – Business Card</title>
<link rel="stylesheet" href="https://fonts.googleapis.com/css2?family=Questrial&family=Roboto:wght@400&display=swap">
<style>
  :root {
    --page-bg: #d4d4d4;
    --card-white: #ffffff;
    --slate: #535e51;
    --slate-deep: #434c40;
    --signal-green: #22e600;
    --ink-grey: #4a4a4a;
    --on-dark: #f2f2f2;
  }
  * { margin: 0; padding: 0; box-sizing: border-box; }
  html, body {
    width: 1200px; height: 1200px; overflow: hidden;
    background: var(--page-bg);
    font-family: "Questrial", "Helvetica Neue", Arial, sans-serif;
  }
  .canvas { position: relative; width: 1200px; height: 1200px; }
  .card {
    position: absolute; left: 250px; width: 700px; height: 400px; overflow: hidden;
  }
  .card--front { top: 170px; background: var(--card-white); }
  .card--back {
    top: 630px;
    background: linear-gradient(to bottom, var(--slate), var(--slate-deep));
  }
  .card-accents { position: absolute; inset: 0; width: 700px; height: 400px; }
  .accent-top { fill: var(--slate); }
  .accent-bottom { fill: var(--signal-green); }
  .contact {
    position: absolute; left: 0; right: 0; top: 146px; text-align: center; color: var(--ink-grey);
  }
  .contact__name { color: var(--signal-green); font-size: 26px; line-height: 30px; }
  .contact__title { font-size: 17px; line-height: 22px; }
  .contact__lines { margin-top: 14px; font-size: 17px; line-height: 21px; }
  .contact__sep { margin: 0 4px; }
  .brand {
    position: absolute; left: 0; right: 0; top: 178px; text-align: center;
    color: var(--signal-green); font-size: 40px; line-height: 44px;
  }
  .brand__mark {
    display: inline-block; width: 18px; height: 18px; background: var(--signal-green);
    margin-right: 14px; vertical-align: 3px;
  }
  .back-url {
    position: absolute; left: 0; right: 0; top: 354px; text-align: center;
    font-family: "Roboto", Arial, sans-serif; font-size: 16px; letter-spacing: 3px;
    color: var(--on-dark);
  }
</style>
</head>
<body>
<main class="canvas">
  <section class="card card--front">
    <svg class="card-accents" viewBox="0 0 700 400" aria-hidden="true">
      <polygon class="accent-top" points="0,0 667,0 605,32 605,14 0,14"/>
      <polygon class="accent-bottom" points="35,400 96,368 96,386 700,386 700,400"/>
    </svg>
    <div class="contact">
      <p class="contact__name">Lukas Varenko</p>
      <p class="contact__title">Fund Manager</p>
      <p class="contact__lines">+1 555 284 6190<span class="contact__sep">|</span>lv@FundCorvel.com<br>www.FundCorvel.com</p>
    </div>
  </section>

  <section class="card card--back">
    <p class="brand"><span class="brand__mark"></span>Corvel Capital</p>
    <p class="back-url">www.FundCorvel.com</p>
  </section>
</main>
</body>
</html>
```